A New and modern Business Card for Tarwick Trade Solutions Ltd

New and modern Logo and Business Card Attached is the current logo/business card designCurrently the business is called "Tarwick & Co." or TTS Ltd for short. This is subject to change.This business specialises in Telecoms and Energy. We work with the major networks (QV, K7, etc) and also offer Energy Products saving clients money off their energy bills.These are business to business services.The current design incorporates a Pheonix, indicating rebirth, starting something new.We would like to maintain the Phoenix element but a newer modern style.We love colours in the logo 3 max.The aim of this is to be ultra slick and modern. I envisage Tarwick & Co. on one side of the card with long descriptions on the other side.Side 1:TTS Ltd/Logo?Side 2:TTS Ltd/Logo/Graphic?Brogan & Co.Name:Address:Phone:Email:The design is mostly flexible but must incorporate a Phoenix.For example "Tarwick & Co." with a block phoenix behind the text...up to you.

Industry/Entity Type

Telecommunications

Contact Information for Business Card

Tarwick & Co.
Address:
Name:
Phone:
Email:

Logo Text

Tarwick & Co.

Colors
33a6d7
0792cd
acd037
9bcb3c
f78f20
fece3e

Requirements
Must have
• Phoenix
• 3/4 colours max
• Blue representing Technology (wireless)
• Green for Eco Energy
• Orange for Phoenix
• White business card background
Should not have
• phoenix must not all be red/ orange fire, we are a technology service company and the phoenix colours must represent this. Fire is not representative of our company.

```html
<!DOCTYPE html>
<html lang="en">
<head>
<meta charset="utf-8">
<title>Tarwick Trade Solutions Limited – Business Card</title>
<link rel="stylesheet" href="https://fonts.googleapis.com/css2?family=Cinzel:wght@500&family=Lato:wght@400;700&display=swap">
<style>
  :root {
    --stage: #2b2b2d;
    --card-white: #ffffff;
    --tech-blue: #0792cd;
    --tech-blue-light: #33a6d7;
    --eco-green: #9bcb3c;
    --eco-green-light: #acd037;
    --phoenix-orange: #f78f20;
    --text-grey: #55585d;
    --rule-grey: #c9ccd0;
    --white: #ffffff;
  }
  * { margin: 0; padding: 0; box-sizing: border-box; }
  html, body { width: 1200px; height: 1108px; overflow: hidden; }
  body {
    background: var(--stage);
    position: relative;
    font-family: "Lato", sans-serif;
  }
  .card {
    position: absolute;
    width: 420px;
    height: 690px;
    border-radius: 26px;
    overflow: hidden;
  }
  /* Front */
  .card--front {
    left: 150px;
    top: 170px;
    background: var(--card-white);
    text-align: center;
  }
  .brand-mark {
    width: 120px;
    height: 120px;
    border-radius: 50%;
    background: var(--phoenix-orange);
    margin: 92px auto 0;
  }
  .brand-name {
    margin-top: 34px;
    font-family: "Cinzel", serif;
    font-weight: 500;
    font-size: 56px;
    letter-spacing: 2px;
    line-height: 1;
    color: var(--tech-blue);
  }
  .brand-tagline {
    margin-top: 8px;
    font-size: 17px;
    letter-spacing: 1.5px;
    color: var(--eco-green);
    text-transform: uppercase;
  }
  .contact {
    margin-top: 80px;
  }
  .contact__name {
    font-size: 24px;
    font-weight: 400;
    color: var(--tech-blue-light);
    text-transform: uppercase;
    letter-spacing: 0.5px;
  }
  .contact__role {
    font-size: 19px;
    color: var(--text-grey);
    margin-top: 2px;
  }
  .contact__line {
    font-size: 19px;
    color: var(--text-grey);
    line-height: 1.35;
  }
  .contact__rule {
    width: 170px;
    height: 1px;
    background: var(--rule-grey);
    margin: 10px auto;
  }
  /* Back */
  .card--back {
    left: 630px;
    top: 250px;
    background: linear-gradient(180deg, var(--tech-blue-light) 0%, var(--tech-blue) 55%, var(--eco-green) 100%);
  }
  .pattern-fill {
    position: absolute;
    inset: 0;
    background: linear-gradient(180deg, rgba(255,255,255,0.08), rgba(172,208,55,0.18));
  }
  .back-brand {
    position: absolute;
    left: 42px;
    bottom: 92px;
  }
  .back-brand__name {
    font-family: "Cinzel", serif;
    font-weight: 500;
    font-size: 60px;
    line-height: 1;
    letter-spacing: 2px;
    color: var(--white);
  }
  .back-brand__tagline {
    margin-top: 6px;
    font-size: 18px;
    letter-spacing: 1.5px;
    color: var(--white);
    text-transform: uppercase;
  }
</style>
</head>
<body>
  <section class="card card--front">
    <div class="brand-mark"></div>
    <div class="brand-name">TARWICK</div>
    <div class="brand-tagline">Trade Solutions Limited</div>
    <div class="contact">
      <div class="contact__name">Daniel Hartley</div>
      <div class="contact__role">Managing Director</div>
      <div class="contact__rule"></div>
      <div class="contact__line">044-555 018 220</div>
      <div class="contact__line">hello@tarwickts.com</div>
      <div class="contact__rule"></div>
      <div class="contact__line">17, Marlow Street</div>
      <div class="contact__line">40318, Northland</div>
    </div>
  </section>

  <section class="card card--back">
    <div class="pattern-fill" role="img" aria-label="Repeating tonal bird-wing pattern across the card face"></div>
    <div class="back-brand">
      <div class="back-brand__name">TARWICK</div>
      <div class="back-brand__tagline">Trade Solutions Limited</div>
    </div>
  </section>
</body>
</html>
```